Women's Jewellery startup needs a captivating, beautifully designed and intuitive online store

[12/24 update]

Added 2 additional documents:

Feedback on designs received so far: designer feedback.docx
Product images from catalogue: products images.docx

Please read the feedback provided on designs provided so far to guide you further on your submission. The product images can be used to create promotional banners for the site.

@@@Added a document (VELISTO JEWELLERY_checklist.docx) which can be used by designers as a checklist when submitting their designs to ensure all aspects of the requirements have been covered @@@

+++IMPORTANT BUT NOT SPECIFIED IN THE REQUIREMENTS DOCUMENT - DESIGN SHOULD INCLUDE SUPPORT FOR MOBILE FRIENDLY SITE TOO+++

***Previous experience designing Jewellery online stores preferred (not essential)***

The name of the online Jewellery store is "Velisto Jewellery" and the business is based in Hong Kong. It will be run by 2 stay at home mothers. We need a Shopify themed store designed that will achieve the following objectives in order of priority:

• Conversion: The primary objective of the design/content is to prompt the customer to make a purchase. While this may sound obvious, it is mentioned so as not to distract the design process by focusing on other objectives (which are also important). The site also needs to be optimized so as to rank high in search engine searches for relevant keywords (SEO)
• Navigation: An intuitive interface which takes away a lot of the thinking from the customer by making it obvious what they need to do when they visit the store
• Engagement: Encourages the customer to spend time on the website and share content with their social network

Where applicable, the design of the store should reflect as closely as possible the mission statements and words outlined below:

• Jewellery you’ll fall in love with
• We want every client to leave the store with a smile
• We want to be able to provide the best service we can in every situation no matter what
• We aim to increase our business by word of mouth; therefore we tell people things about our store that makes it interesting for them to share
• We love every customer, no matter how difficult things get
• We, as a team, are so well informed about our products and brands that we always have the best information for our customers
• We celebrate women here!
• We celebrate life in here!
• We celebrate beauty here!
• We celebrate families here, as jewellery often stays within families.
• We will always try to make an extra step
• We will always try to exceed the expectation of our customers
• We will go as far as we possibly can to attract a customer back to our store and connect with us
• Every client that leaves our store knows more about jewellery because we passionately told him about it
• Romantic, classic, love, warm, cool, stylish

A draft functional specification is attached with this brief. We would like the design to reflect as closely as possible the functional requirements outlined in the document. Open to suggestions to improve upon the functional requirements.

Target Market(s)

Women aged 18-55

Industry/Entity Type

Jewelry Store

Coding

Coded - Design and coding required

Number of Pages Required

5+ page

Font styles to use
Other font styles liked:
• Myriad Pro as per Logo but open to any font that complements this one

Requirements
Must have
• 1. A look that encourages the user to make a purchase
• 2. An intuitive, easy to navigate and engaging interface
• 3. Primary colour scheme as defined in the functional specification attached
• 4. Simplistic look, not too cluttered
Nice to have
• 1. Closely matching the functional requirements of the site as outlined in the requirements specification but open to any better ideas

```html
<!DOCTYPE html>
<html lang="en">
<head>
<meta charset="utf-8">
<title>Velisto Jewellery</title>
<link rel="stylesheet" href="https://fonts.googleapis.com/css2?family=Cormorant+Garamond:wght@500;600;700&family=Open+Sans:wght@400;600&display=swap">
<style>
  :root {
    --black: #000000;
    --gold: #c9962d;
    --panel: #e6e7ea;
    --panel-light: #eef0f2;
    --white: #ffffff;
    --ink: #1c1c1c;
    --field: #3a3a3a;
    --serif: "Cormorant Garamond", Georgia, serif;
    --sans: "Open Sans", Arial, sans-serif;
  }
  * { box-sizing: border-box; margin: 0; padding: 0; }
  html, body { width: 1200px; height: 2605px; overflow: hidden; background: var(--white); }
  body { position: relative; font-family: var(--serif); color: var(--ink); }

  .site-header { position: absolute; left: 0; top: 0; width: 1200px; height: 186px; background: var(--black); }
  .menu-toggle { position: absolute; left: 74px; top: 63px; }
  .brand { position: absolute; left: 0; right: 0; top: 52px; text-align: center; color: var(--gold); font-size: 34px; font-weight: 600; letter-spacing: 8px; }
  .header-tools { position: absolute; right: 74px; top: 62px; display: flex; align-items: center; gap: 10px; color: var(--white); font-family: var(--sans); font-size: 14px; }
  .header-tools .sep { color: var(--white); }
  .header-tools .count { color: var(--gold); }
  .main-nav { position: absolute; left: 0; right: 0; top: 147px; display: flex; justify-content: center; gap: 42px; }
  .main-nav a { color: var(--white); text-decoration: none; font-size: 14px; font-weight: 600; letter-spacing: 0.5px; }

  .hero { position: absolute; left: 0; top: 186px; width: 1200px; height: 483px; overflow: hidden; }
  .hero-visual { position: absolute; inset: 0;
    background:
      radial-gradient(circle at 12% 25%, #8a6a55 0, transparent 22%),
      radial-gradient(circle at 70% 20%, #b07a2a 0, transparent 20%),
      radial-gradient(circle at 85% 70%, #9c6a20 0, transparent 24%),
      radial-gradient(circle at 30% 80%, #5e4e48 0, transparent 22%),
      radial-gradient(circle at 55% 65%, #cfc6c0 0, transparent 18%),
      linear-gradient(135deg, #6f5a50 0%, #a57a45 40%, #7b6a63 70%, #b5842f 100%); }
  .hero-shade { position: absolute; inset: 0; background: rgba(0,0,0,0.18); }
  .hero-title { position: absolute; left: 0; right: 0; top: 160px; text-align: center; color: var(--white); font-size: 46px; font-weight: 700; line-height: 48px; }
  .btn { display: block; position: absolute; text-align: center; text-decoration: none; font-family: var(--serif); font-weight: 600; letter-spacing: 0.5px; }
  .btn-dark { left: 516px; top: 283px; width: 167px; height: 42px; line-height: 38px; border: 2px solid var(--gold); background: rgba(0,0,0,0.7); color: var(--white); font-size: 15px; }
  .slider-dots { position: absolute; left: 0; right: 0; top: 437px; display: flex; justify-content: center; gap: 7px; }
  .slider-dots span { width: 10px; height: 10px; border-radius: 50%; background: var(--white); }
  .slider-dots span.active { background: var(--gold); }

  .promo { position: absolute; left: 0; width: 1200px; overflow: hidden; }
  .promo-copy { position: absolute; width: 500px; text-align: center; }
  .promo-title { font-size: 32px; font-weight: 500; line-height: 38px; color: var(--ink); letter-spacing: 0.5px; }
  .btn-outline { position: relative; margin: 34px auto 0; width: 168px; height: 43px; line-height: 39px; border: 2px solid var(--gold); color: var(--ink); font-size: 14px; }
  .promo-visual { position: absolute; }

  .promo-bride { top: 669px; height: 406px; background: var(--panel); }
  .promo-bride .promo-visual { left: 0; top: 0; width: 700px; height: 406px;
    background: linear-gradient(90deg, #3a3a3a 0%, #8d8d8d 35%, #c9c9c9 60%, rgba(230,231,234,0) 100%); }
  .promo-bride .promo-copy { left: 670px; top: 130px; }

  .promo-vintage { top: 1075px; height: 406px; background: radial-gradient(ellipse at 70% 55%, #fbfbfc 0, var(--panel) 70%); }
  .promo-vintage .promo-copy { left: 90px; top: 125px; }
  .promo-vintage .promo-visual { left: 668px; top: 45px; width: 405px; height: 313px;
    background: radial-gradient(ellipse at 50% 50%, #7a1020 0, #9a1a2a 14%, #b9b9bd 30%, #dcdcdf 55%, rgba(238,240,242,0) 72%); }

  .promo-charm { top: 1481px; height: 403px; background: linear-gradient(90deg, #eef0f2 0%, var(--panel) 100%); }
  .promo-charm .promo-visual { left: 153px; top: 35px; width: 420px; height: 325px;
    background: radial-gradient(ellipse at 45% 58%, #cfa548 0, #d9d9dc 30%, #e9e9eb 55%, rgba(238,240,242,0) 72%); }
  .promo-charm .promo-copy { left: 611px; top: 130px; }

  .promo-men { top: 1884px; height: 396px; background: var(--white); }
  .promo-men .promo-copy { left: 50px; top: 130px; }
  .promo-men .promo-visual { left: 643px; top: 52px; width: 373px; height: 278px;
    background: radial-gradient(ellipse at 45% 50%, #e8b236 0, #d39a1e 35%, #b27d12 55%, rgba(255,255,255,0) 72%); }

  .site-footer { position: absolute; left: 0; top: 2280px; width: 1200px; height: 325px; background: var(--black); color: var(--white); text-align: center; }
  .newsletter-title { position: absolute; left: 0; right: 0; top: 40px; font-size: 21px; font-weight: 500; }
  .newsletter-form { position: absolute; left: 465px; top: 77px; width: 270px; height: 45px; display: flex; }
  .newsletter-field { width: 221px; height: 45px; background: var(--field); color: var(--white); font-family: var(--sans); font-size: 13px; text-align: left; padding-left: 12px; line-height: 45px; }
  .newsletter-submit { width: 49px; height: 45px; background: var(--gold); display: flex; align-items: center; justify-content: center; }
  .footer-nav { position: absolute; left: 0; right: 0; top: 173px; display: flex; justify-content: center; gap: 38px; }
  .footer-nav a { color: var(--white); text-decoration: none; font-size: 12px; font-weight: 600; letter-spacing: 0.3px; }
  .copyright { position: absolute; left: 0; right: 0; top: 213px; font-size: 11px; }
  .social { position: absolute; left: 0; right: 0; top: 250px; display: flex; justify-content: center; gap: 22px; }
  .social span { width: 16px; height: 16px; border-radius: 50%; background: var(--white); }
</style>
</head>
<body>
  <header class="site-header">
    <svg class="menu-toggle" width="18" height="16" viewBox="0 0 18 16" aria-label="Menu">
      <rect x="0" y="1" width="18" height="2.5" fill="#fff"/>
      <rect x="0" y="6.75" width="18" height="2.5" fill="#fff"/>
      <rect x="0" y="12.5" width="18" height="2.5" fill="#fff"/>
    </svg>
    <div class="brand">VELISTO</div>
    <div class="header-tools">
      <svg width="14" height="14" viewBox="0 0 14 14" aria-label="Search"><circle cx="6" cy="6" r="4.3" fill="none" stroke="#fff" stroke-width="2"/><line x1="9" y1="9" x2="13" y2="13" stroke="#fff" stroke-width="2.2"/></svg>
      <span class="sep">/</span>
      <svg width="13" height="14" viewBox="0 0 13 14" aria-label="Account"><circle cx="6.5" cy="4" r="3.2" fill="#fff"/><path d="M0.5 14 C0.5 8.5 12.5 8.5 12.5 14 Z" fill="#fff"/></svg>
      <span class="sep">/</span>
      <svg width="16" height="14" viewBox="0 0 16 14" aria-label="Cart"><path d="M0 1 H3 L5 9 H13 L15 3 H4" fill="none" stroke="#fff" stroke-width="1.8"/><circle cx="6" cy="12" r="1.5" fill="#fff"/><circle cx="12" cy="12" r="1.5" fill="#fff"/></svg>
      <span class="count">(0)</span>
    </div>
    <nav class="main-nav">
      <a href="#">ABOUT US</a><a href="#">WOMEN</a><a href="#">MEN</a><a href="#">ENGAGEMENT</a><a href="#">VELISTO COLLECTIONS</a><a href="#">GIFT</a>
    </nav>
  </header>

  <section class="hero">
    <div class="hero-visual" role="img" aria-label="Assorted cut gemstones in amber, smoky and pink tones with a pearl"></div>
    <div class="hero-shade"></div>
    <h1 class="hero-title">Add Colour and Vibrancy<br>to your Life</h1>
    <a class="btn btn-dark" href="#">SHOP</a>
    <div class="slider-dots"><span></span><span class="active"></span><span></span></div>
  </section>

  <section class="promo promo-bride">
    <div class="promo-visual" role="img" aria-label="Black and white photo of a bride in lace wearing drop earrings"></div>
    <div class="promo-copy">
      <h2 class="promo-title">'SHINE ON THE BRIDE'<br>MOSSANITE COLLECTION</h2>
      <a class="btn btn-outline" href="#">SHOP NOW</a>
    </div>
  </section>

  <section class="promo promo-vintage">
    <div class="promo-copy">
      <h2 class="promo-title">‘TIMELESS’<br>VINTAGE COLLECTION</h2>
      <a class="btn btn-outline" href="#">SHOP NOW</a>
    </div>
    <div class="promo-visual" role="img" aria-label="Vintage silver ring with an oval red gemstone"></div>
  </section>

  <section class="promo promo-charm">
    <div class="promo-visual" role="img" aria-label="Silver charm with a gold tree of life"></div>
    <div class="promo-copy">
      <h2 class="promo-title">‘ESSENCE’<br>CHARM COLLECTION</h2>
      <a class="btn btn-outline" href="#">SHOP NOW</a>
    </div>
  </section>

  <section class="promo promo-men">
    <div class="promo-copy">
      <h2 class="promo-title">‘AMOUR’<br>MEN COLLECTION</h2>
      <a class="btn btn-outline" href="#">SHOP NOW</a>
    </div>
    <div class="promo-visual" role="img" aria-label="Gold signet ring with an engraved crest"></div>
  </section>

  <footer class="site-footer">
    <div class="newsletter-title">Sign Up Newsletter</div>
    <div class="newsletter-form">
      <div class="newsletter-field">Email Address</div>
      <div class="newsletter-submit">
        <svg width="18" height="12" viewBox="0 0 18 12" aria-label="Submit"><path d="M0 6 H15 M10 1 L16 6 L10 11" fill="none" stroke="#fff" stroke-width="2.2"/></svg>
      </div>
    </div>
    <nav class="footer-nav">
      <a href="#">CONTACT US</a><a href="#">SHIPPING</a><a href="#">RETURN POLICY</a><a href="#">JEWELLERY CARE</a><a href="#">WHOLESALE ENQUIRIES</a><a href="#">TERMS &amp; CONDITIONS</a><a href="#">SIZE GUIDE</a>
    </nav>
    <div class="copyright">Copyright © 2017. Company Name. All Right Reserved</div>
    <div class="social" aria-label="Social links"><span></span><span></span><span></span><span></span></div>
  </footer>
</body>
</html>
```